Brevik Summitline Builders

I own a roofing business Brevikroofing.com and I want to get a Facebook page YouTube Chanel Instagram twitter all the platforms I can add my business to

```html
<!DOCTYPE html>
<html lang="en">
<head>
<meta charset="utf-8">
<title>Brevik Summitline Builders – Cover Banner</title>
<link href="https://fonts.googleapis.com/css2?family=Roboto:wght@700;900&family=Open+Sans:wght@400;600&display=swap" rel="stylesheet">
<style>
  :root{
    --page-bg:#eef0f4;
    --navy:#0f2440;
    --red:#ee1c25;
    --sky:#1f7be0;
    --house:#f3ecc4;
    --roof:#5a3a24;
    --white:#ffffff;
    --rule:#c9d1dc;
    --body-text:#e4e9f0;
  }
  *{margin:0;padding:0;box-sizing:border-box}
  html,body{width:1200px;height:1200px;overflow:hidden;background:var(--page-bg)}
  .canvas{width:1200px;height:1200px;display:flex;align-items:center;justify-content:center}
  .cover{position:relative;width:1100px;height:418px;overflow:hidden;background:var(--navy)}
  .cover-shapes{position:absolute;inset:0}
  .logo{position:absolute;top:0;right:0;width:165px;height:73px;display:flex;align-items:center;justify-content:center;gap:7px;padding-left:24px}
  .logo-mark{width:12px;height:12px;background:var(--red)}
  .logo-name{font-family:"Roboto",sans-serif;font-weight:700;font-size:22px;letter-spacing:2px;color:var(--navy)}
  .headline{position:absolute;right:20px;top:92px;text-align:right;font-family:"Roboto",sans-serif;font-weight:900;color:var(--white);line-height:1.08;text-transform:uppercase}
  .headline-main{display:block;font-size:37px}
  .headline-sub{display:block;font-size:24px;font-weight:700;margin-top:4px}
  .headline-place{display:block;font-size:33px;margin-top:6px}
  .intro{position:absolute;left:668px;width:410px;top:216px;text-align:center;font-family:"Open Sans",sans-serif;font-size:14px;line-height:1.36;color:var(--body-text)}
  .divider{position:absolute;left:672px;right:4px;top:286px;height:1px;background:var(--rule)}
  .contact{position:absolute;font-family:"Open Sans",sans-serif;font-size:15px;line-height:20px;color:var(--white);display:flex;align-items:center;gap:7px;letter-spacing:.3px;white-space:nowrap}
  .contact svg{width:13px;height:13px;fill:var(--white);flex:none}
  .contact-phone{left:686px;top:305px;font-size:16px}
  .contact-email{left:872px;top:305px}
  .contact-web{left:792px;top:337px;font-size:16px}
</style>
</head>
<body>
<main class="canvas">
  <section class="cover">
    <svg class="cover-shapes" viewBox="0 0 1100 418" width="1100" height="418">
      <defs>
        <linearGradient id="photo-tone" x1="0" y1="0" x2="0.3" y2="1">
          <stop offset="0" stop-color="#1f7be0"/>
          <stop offset="0.35" stop-color="#4b6fa8"/>
          <stop offset="0.55" stop-color="#5a3a24"/>
          <stop offset="1" stop-color="#f3ecc4"/>
        </linearGradient>
      </defs>
      <rect class="house-photo" role="img" aria-label="Photo of a cream two-storey house with steep brown shingle roof gables against a blue sky" x="0" y="0" width="700" height="418" fill="url(#photo-tone)"/>
      <polygon class="accent-red" points="0,0 93,0 179,418 0,418" fill="#ee1c25"/>
      <polygon class="info-panel" points="570,0 1100,0 1100,418 670,418" fill="#0f2440"/>
      <polygon class="logo-plate" points="935,0 1100,0 1100,73 955,73" fill="#ffffff"/>
    </svg>

    <div class="logo">
      <span class="logo-mark"></span>
      <span class="logo-name">BREVIK</span>
    </div>

    <h1 class="headline">
      <span class="headline-main">#1 Roof Replacement &amp;</span>
      <span class="headline-sub">Repair Services Contractor</span>
      <span class="headline-place">In Metro St. Louis</span>
    </h1>

    <p class="intro">Brevik Summitline Builders has over 14 years experience as a roofing contractor in the Metro St. Louis Region. Trust your home to a local expert in roofing.</p>

    <div class="divider"></div>

    <div class="contact contact-phone">
      <svg viewBox="0 0 24 24"><path d="M6.6 10.8a15.1 15.1 0 0 0 6.6 6.6l2.2-2.2a1 1 0 0 1 1-.25 11.4 11.4 0 0 0 3.6.57 1 1 0 0 1 1 1V20a1 1 0 0 1-1 1A17 17 0 0 1 3 4a1 1 0 0 1 1-1h3.5a1 1 0 0 1 1 1c0 1.25.2 2.45.57 3.57a1 1 0 0 1-.25 1z"/></svg>
      <span>(555) 014-2290</span>
    </div>
    <div class="contact contact-email">
      <svg viewBox="0 0 24 24"><path d="M2 5h20v14H2z"/><path d="M2 5l10 8 10-8" stroke="#0f2440" stroke-width="1.6" fill="none"/></svg>
      <span>brevikroofing@mail.com</span>
    </div>
    <div class="contact contact-web">
      <svg viewBox="0 0 24 24"><circle cx="12" cy="12" r="10"/><path d="M2 12h20M12 2c3 3 3 17 0 20M12 2c-3 3-3 17 0 20" stroke="#0f2440" stroke-width="1.4" fill="none"/></svg>
      <span>brevikroofing.com</span>
    </div>
  </section>
</main>
</body>
</html>
```